Ridgeline Journeys business card

please see website
www.ridgelinejourneys.comau

info needed on card
Curtis Halvey
Ph
email
Adventure Riding GPS trails

please use my logo and colours off my site

Curtis Halvey
curtis@ridgelinejourneys.com

```html
<!DOCTYPE html>
<html lang="en">
<head>
<meta charset="utf-8">
<title>Ridgeline Journeys – Business Card</title>
<link href="https://fonts.googleapis.com/css2?family=Open+Sans:wght@400;700&display=swap" rel="stylesheet">
<style>
  :root {
    --backdrop: #3b3b3b;
    --card: #1b1b1b;
    --card-edge: #262626;
    --accent: #f5c800;
    --text-light: #f2f2f2;
    --mark-grey: #6e6e6e;
    --divider: #2e2e2e;
  }
  * { margin: 0; padding: 0; box-sizing: border-box; }
  html, body {
    width: 1200px;
    height: 900px;
    overflow: hidden;
    background: var(--backdrop);
    font-family: "Open Sans", Arial, sans-serif;
  }
  .canvas {
    position: relative;
    width: 1200px;
    height: 900px;
  }
  .card {
    position: absolute;
    top: 300px;
    width: 520px;
    height: 300px;
    background: var(--card);
    border: 1px solid var(--card-edge);
    border-radius: 20px;
    box-shadow: 0 10px 30px rgba(0,0,0,0.35);
  }
  .card--front { left: 60px; }
  .card--back { left: 620px; }

  /* Front */
  .brand-block {
    position: absolute;
    left: 40px;
    top: 92px;
    width: 170px;
    display: flex;
    flex-direction: column;
    align-items: center;
    gap: 14px;
  }
  .brand-dot {
    width: 56px;
    height: 56px;
    border-radius: 50%;
    background: var(--mark-grey);
  }
  .brand-name {
    color: var(--accent);
    font-weight: 700;
    font-size: 17px;
    text-align: center;
    line-height: 1.2;
  }
  .divider {
    position: absolute;
    left: 232px;
    top: 40px;
    width: 1px;
    height: 160px;
    background: var(--divider);
  }
  .contact {
    position: absolute;
    left: 252px;
    top: 66px;
  }
  .contact__name {
    color: var(--accent);
    font-weight: 700;
    font-size: 17px;
    margin-bottom: 8px;
  }
  .contact__row {
    display: flex;
    align-items: center;
    gap: 8px;
    color: var(--text-light);
    font-size: 13.5px;
    line-height: 23px;
  }
  .contact__icon {
    width: 14px;
    height: 14px;
    border-radius: 3px;
    background: var(--accent);
    display: flex;
    align-items: center;
    justify-content: center;
  }
  .tagline {
    position: absolute;
    left: 232px;
    top: 232px;
    color: var(--accent);
    font-weight: 700;
    font-size: 17px;
  }

  /* Back */
  .back-brand {
    position: absolute;
    left: 80px;
    top: 100px;
    display: flex;
    align-items: center;
    gap: 18px;
  }
  .back-brand .brand-dot { width: 64px; height: 64px; }
  .back-brand__name {
    color: var(--text-light);
    font-weight: 700;
    font-size: 26px;
    text-transform: uppercase;
    line-height: 1.05;
  }
  .back-url {
    position: absolute;
    left: 250px;
    top: 205px;
    color: var(--text-light);
    font-size: 13px;
  }
</style>
</head>
<body>
<div class="canvas">

  <section class="card card--front">
    <div class="brand-block">
      <div class="brand-dot"></div>
      <div class="brand-name">Ridgeline Journeys</div>
    </div>

    <div class="divider"></div>

    <div class="contact">
      <div class="contact__name">Curtis Halvey</div>
      <div class="contact__row">
        <span class="contact__icon">
          <svg width="10" height="10" viewBox="0 0 10 10"><path d="M2 1 L4 1 L4.6 3 L3.5 3.8 Q4.6 5.8 6.2 6.6 L7 5.5 L9 6 L9 8 Q5 9 2.5 6 Q1 4 2 1 Z" fill="#1b1b1b"/></svg>
        </span>
        (045)-312-6084
      </div>
      <div class="contact__row">
        <span class="contact__icon">
          <svg width="10" height="10" viewBox="0 0 10 10"><rect x="1" y="2.5" width="8" height="5.5" fill="none" stroke="#1b1b1b" stroke-width="1.2"/><path d="M1 2.5 L5 5.5 L9 2.5" fill="none" stroke="#1b1b1b" stroke-width="1.2"/></svg>
        </span>
        curtis@ridgelinejourneys.com
      </div>
      <div class="contact__row">
        <span class="contact__icon">
          <svg width="10" height="10" viewBox="0 0 10 10"><circle cx="5" cy="5" r="3.6" fill="none" stroke="#1b1b1b" stroke-width="1.2"/><path d="M1.4 5 H8.6 M5 1.4 Q3 5 5 8.6 M5 1.4 Q7 5 5 8.6" fill="none" stroke="#1b1b1b" stroke-width="0.9"/></svg>
        </span>
        www.ridgelinejourneys.comau
      </div>
    </div>

    <div class="tagline">Adventure Riding GPS trails</div>
  </section>

  <section class="card card--back">
    <div class="back-brand">
      <div class="brand-dot"></div>
      <div class="back-brand__name">Ridgeline<br>Journeys</div>
    </div>
    <div class="back-url">www.ridgelinejourneys.comau</div>
  </section>

</div>
</body>
</html>
```